Car rental website design for a UAE car rental company

This project is about creating a new website design for a car rental company located in Dubai (United Arab Emirates), I opened the same project a few months ago but I didn't receive a lot of appealing entries so I closed it but this time I am marking the project as guaranteed to avoid such situation again, if you have already provided a design before then please re-submit again on this project so that it is considered while reviewing all the designs

A few important things:

1- We need a simple non-complex design
2- The final deliverable would be 2 screens (PSD, JPEG ... etc), the first screen is for the home page and the second screen is for an internal page
3- The home page must have a section that end users can use to rent a car online directly from the home page instead of going into some inner pages
4- The current website is very old and not very appealing so avoid creating a similar design (www.crestvane-autos.example)
5- The name is Crestvane but the company rents normal cars (no Limousin cars will be rented) so avoid adding any fancy cars in the images/graphics used in the design, just normal end users cars
6- The expected pages would be: home, About us, Our team, Strategy, Contact us and links to social media pages
7- The attachments include the company's logo and some screens from other car rental companies that provide online rentals/payments

If you have any questions please feel free to ask and please note that we will need the designs urgently

Thanks

Target Market(s)

Dubai - United Arab Emirates

Industry/Entity Type

It Company

Number of Pages Required

2 page

Font styles to use
Sans Serif

Requirements
Must have
• Check the project details
Nice to have
Should not have

```html
<!DOCTYPE html>
<html lang="en">
<head>
<meta charset="utf-8">
<title>Crestvane – Home</title>
<link href="https://fonts.googleapis.com/css2?family=Open+Sans:ital,wght@0,400;0,600;0,700;1,400&display=swap" rel="stylesheet">
<style>
:root{
  --black:#000;
  --nav:#333;
  --nav-active:#1e1e1e;
  --panel:#2b2b2b;
  --white:#fff;
  --text:#333;
  --muted:#777;
  --panel-text:#bdbdbd;
  --field:#5a5a5a;
  --line:#ccc;
  --accent:#b0203a;
}
*{margin:0;padding:0;box-sizing:border-box}
html,body{width:1200px;height:2609px;overflow:hidden}
body{position:relative;background:var(--white);font-family:"Open Sans",Arial,sans-serif;color:var(--text)}
.abs{position:absolute}

/* header */
.topbar{left:0;top:0;width:1200px;height:104px;background:var(--black)}
.brand{left:70px;top:34px;display:flex;align-items:center;gap:12px;color:var(--white);font-size:28px;font-weight:600}
.brand-mark{width:34px;height:34px;background:var(--accent)}
.callout{left:850px;top:22px;width:205px;text-align:right;color:var(--white)}
.callout small{display:block;font-size:11px;line-height:14px}
.callout strong{display:block;font-size:19px;font-weight:600;margin-top:6px;letter-spacing:.5px;white-space:nowrap}
.callout-dot{left:1066px;top:28px;width:38px;height:38px}

.mainnav{left:0;top:104px;width:1200px;height:58px;background:var(--nav);display:flex;padding-left:101px}
.mainnav a{color:var(--white);text-decoration:none;font-size:14px;line-height:58px;padding:0 19px;margin-right:6px}
.mainnav a.active{background:var(--nav-active)}

/* hero */
.hero{left:0;top:162px;width:1200px;height:551px;
  background:radial-gradient(ellipse at 75% 35%,#e0c98a 0%,#9a7a3c 25%,#3d3020 55%,#141210 100%)}
.hero-copy{left:600px;top:305px;width:450px;text-align:center;color:#111}
.hero-copy h1{font-size:40px;font-weight:600;line-height:54px}
.hero-copy p{font-size:15px;font-weight:700;line-height:20px;margin-top:6px}
.hero-btn{left:739px;top:456px;width:197px;height:33px;background:#111;color:var(--white);font-size:15px;text-align:center;line-height:33px}
.hero-arrow{top:366px}
.dots span{position:absolute;top:701px;height:3px;background:#888}

/* welcome */
.welcome{left:100px;top:748px;width:1000px;text-align:center}
.welcome h2{font-size:30px;font-weight:600;color:#111}
.welcome p{font-size:13px;line-height:20px;margin-top:14px;padding:0 15px}
.btn-dark{background:#111;color:var(--white);font-size:13px;display:inline-block}
.call-btn{left:532px;top:925px;width:131px;height:30px;line-height:30px;text-align:center}

/* services */
.services{left:101px;top:1009px;width:998px;height:358px;background:var(--panel);color:var(--white);text-align:center}
.services h2{font-size:30px;font-weight:400;margin-top:26px}
.services p.lead{font-size:12.5px;line-height:19px;color:var(--panel-text);margin:8px 60px 0}
.service{position:absolute;top:178px;width:220px;text-align:center;font-size:14px;line-height:20px}
.service svg{display:block;margin:0 auto 14px}

/* testimonials */
.testi h2{left:0;top:1408px;width:1200px;text-align:center;font-size:30px;font-weight:600;color:#111}
.avatar{left:560px;top:1485px;width:77px;height:77px;border-radius:50%;background:linear-gradient(#8a6a54,#3c2c22)}
.quote{left:220px;top:1583px;width:760px;text-align:center;font-style:italic;color:var(--muted);font-size:15px;line-height:22px}

/* reservations */
.booking{left:0;top:1722px;width:1200px;height:749px;background:radial-gradient(ellipse at 60% 60%,#3a3a3a 0%,#1a1a1a 55%,#0c0c0c 100%)}
.booking-head{left:0;top:1748px;width:1200px;text-align:center;color:var(--white)}
.booking-head h2{font-size:30px;font-weight:400}
.booking-head p{font-size:14px;font-weight:600;margin-top:2px}
.label{color:var(--white);font-size:17px;font-weight:600}
.field{background:var(--field);height:38px}
.tiny{color:#aaa;font-size:11px}
.ampm{color:var(--white);font-size:13px;line-height:38px;padding-left:12px}
.sub-head{left:0;top:2155px;width:1200px;text-align:center;color:#ddd;font-size:17px}
.check{color:#ddd;font-size:14px;display:flex;align-items:center;gap:16px}
.check i{width:17px;height:17px;background:#bbb;display:block}
.check i.on{background:var(--white);border:4px solid #444;outline:1px solid #bbb}
.note-label{left:104px;top:2272px;color:#ddd;font-size:14px}
.btn-light{left:377px;top:2409px;width:211px;height:38px;background:var(--white);color:#111;text-align:center;line-height:38px;font-size:15px;font-weight:600}
.btn-ghost{left:610px;top:2409px;width:209px;height:38px;border:2px solid var(--white);color:var(--white);text-align:center;line-height:34px;font-size:14px}

/* footer */
.footnav{left:0;top:2503px;width:1200px;text-align:center;font-size:11px;color:#555}
.footnav span{margin:0 14px;color:#888}
.footrule{left:101px;top:2543px;width:998px;height:1px;background:var(--line)}
.copyright{left:101px;top:2567px;font-size:12px;color:#333}
.social{left:994px;top:2568px;display:flex;gap:14px}
.social i{width:16px;height:16px;border-radius:50%;background:#111;display:block}
</style>
</head>
<body>

<header>
  <div class="abs topbar"></div>
  <div class="abs brand"><span class="brand-mark"></span>Crestvane</div>
  <div class="abs callout"><small>Call Us For Immediate<br>Car Service</small><strong>555 - 014 - 2290</strong></div>
  <svg class="abs callout-dot" width="38" height="38" viewBox="0 0 38 38"><circle cx="19" cy="19" r="16" fill="none" stroke="#fff" stroke-width="3"/><path d="M13 11l4 0 1 5-2 2c1 2 3 4 5 5l2-2 5 1 0 4c-8 0-15-7-15-15z" fill="#fff"/></svg>
  <nav class="abs mainnav">
    <a class="active">Home</a><a>About Us</a><a>Available Services</a><a>Service Area</a><a>On-Line Reservations</a><a>Credit Card Form</a><a>Our Fleet</a><a>Contact Us</a>
  </nav>
</header>

<section>
  <div class="abs hero" role="img" aria-label="Photo of a family car side mirror passing city lights at night"></div>
  <div class="abs hero-copy">
    <h1>Crestvane</h1>
    <p>Morbi euismod interdum tortor sed consequat. Praesent lacinia arcu nec ipsum pellentesque placerat. Vestibulum feugiat at arcu nec tempor.</p>
  </div>
  <div class="abs hero-btn">Book a reservation</div>
  <svg class="abs hero-arrow" style="left:43px" width="32" height="32" viewBox="0 0 32 32"><circle cx="16" cy="16" r="14" fill="none" stroke="#ccc" stroke-width="2"/><path d="M19 9l-7 7 7 7" fill="none" stroke="#ccc" stroke-width="2"/></svg>
  <svg class="abs hero-arrow" style="left:1135px" width="32" height="32" viewBox="0 0 32 32"><circle cx="16" cy="16" r="14" fill="none" stroke="#ccc" stroke-width="2"/><path d="M13 9l7 7-7 7" fill="none" stroke="#ccc" stroke-width="2"/></svg>
  <div class="dots"><span style="left:456px;width:80px;background:#222"></span><span style="left:550px;width:90px"></span><span style="left:654px;width:85px"></span></div>
</section>

<section>
  <div class="abs welcome">
    <h2>Welcome To Crestvane</h2>
    <p>Crestvane Car Rental was established in 2010 in Dubai, United Arab Emirates. Our team of friendly rental advisors strives to achieve one goal, to make every trip across the Emirates as easy and comfortable as possible. From compact city cars to roomy family sedans and SUVs, every vehicle is clean, insured and ready to drive. Book online in minutes, pick up at the airport or your hotel, and enjoy the road with your one stop shop for everyday car rental.</p>
  </div>
  <div class="abs btn-dark call-btn">Call the number</div>
</section>

<section class="abs services">
  <h2>Available Services</h2>
  <p class="lead">We can accommodate all your car rental needs in Dubai. Whether you are in a hurry to get to the airport, touring the city at your own pace, headed to the beach or driving to another emirate, we will surpass your expectations with proven reliability and unparalleled attention.</p>
  <div class="service" style="left:22px">
    <svg width="52" height="52" viewBox="0 0 52 52"><path d="M48 10c-2-2-6 0-9 3l-8 8-20-6-4 4 16 10-7 7-6-1-3 3 8 5 5 8 3-3-1-6 7-7 10 16 4-4-6-20 8-8c3-3 5-7 3-9z" fill="#fff"/></svg>
    Airport, Cruise Terminal &amp;<br>Metro Station
  </div>
  <div class="service" style="left:264px">
    <svg width="52" height="52" viewBox="0 0 52 52"><circle cx="26" cy="29" r="17" fill="none" stroke="#fff" stroke-width="3"/><path d="M26 19v10l7 5" fill="none" stroke="#fff" stroke-width="3"/><path d="M8 13l7-6M44 13l-7-6" stroke="#fff" stroke-width="3"/></svg>
    Hourly Rentals
  </div>
  <div class="service" style="left:505px">
    <svg width="52" height="52" viewBox="0 0 52 52"><circle cx="26" cy="26" r="21" fill="#fff"/><circle cx="29" cy="21" r="7" fill="none" stroke="#2b2b2b" stroke-width="3"/><path d="M24 26l-9 10" stroke="#2b2b2b" stroke-width="4"/></svg>
    City-to-City
  </div>
  <div class="service" style="left:746px">
    <svg width="52" height="52" viewBox="0 0 52 52"><circle cx="26" cy="26" r="21" fill="#fff"/><path d="M26 14l-10 10h6v14h8V24h6z" fill="#2b2b2b"/></svg>
    Daily &amp; Weekly Car Rental
  </div>
</section>

<section class="testi">
  <h2 class="abs">Testimonials</h2>
  <div class="abs avatar" role="img" aria-label="Customer portrait photo"></div>
  <svg class="abs" style="left:101px;top:1586px" width="28" height="28" viewBox="0 0 28 28"><circle cx="14" cy="14" r="12" fill="none" stroke="#333" stroke-width="2"/><path d="M20 14H8M12 9l-5 5 5 5" fill="none" stroke="#333" stroke-width="2"/></svg>
  <p class="abs quote">Morbi euismod interdum tortor sed consequat. Praesent lacinia arcu nec ipsum pellentesque placerat. Vestibulum feugiat at arcu nec tempor. Quisque ante magna, porttitor euismod tortor eget, pellentesque facilisis dui. Fusce condimentum magna gravida consectetur</p>
  <svg class="abs" style="left:1073px;top:1586px" width="28" height="28" viewBox="0 0 28 28"><circle cx="14" cy="14" r="12" fill="none" stroke="#333" stroke-width="2"/><path d="M8 14h12M16 9l5 5-5 5" fill="none" stroke="#333" stroke-width="2"/></svg>
</section>

<section>
  <div class="abs booking" role="img" aria-label="Blurred dark photo of a car interior at night"></div>
  <div class="abs booking-head"><h2>On-Line Reservations</h2><p>All reservations must be made at least 12 hours in advance.</p></div>

  <div class="abs label" style="left:101px;top:1894px">Pick-up Date :</div>
  <div class="abs field" style="left:336px;top:1888px;width:252px"></div>
  <svg class="abs" style="left:556px;top:1897px" width="20" height="20" viewBox="0 0 20 20"><rect x="1" y="2" width="18" height="17" fill="none" stroke="#222" stroke-width="2"/><path d="M1 7h18M6 10v7M10 10v7M14 10v7M1 13h18" stroke="#222" stroke-width="1.5"/></svg>
  <div class="abs label" style="left:614px;top:1894px">Pick-up Time :</div>
  <div class="abs tiny" style="left:848px;top:1867px">HH</div>
  <div class="abs tiny" style="left:936px;top:1867px">MM</div>
  <div class="abs field" style="left:849px;top:1888px;width:76px"></div>
  <div class="abs field" style="left:936px;top:1888px;width:76px"></div>
  <div class="abs field ampm" style="left:1023px;top:1888px;width:76px">AM<svg style="position:absolute;right:12px;top:16px" width="9" height="6" viewBox="0 0 9 6"><path d="M0 0h9L4.5 6z" fill="#fff"/></svg></div>

  <div class="abs label" style="left:101px;top:1955px">Number of Passangers :</div>
  <div class="abs field" style="left:336px;top:1949px;width:252px"></div>
  <div class="abs label" style="left:614px;top:1955px">Pick-up Location :</div>
  <div class="abs field" style="left:849px;top:1949px;width:250px"></div>

  <div class="abs label" style="left:101px;top:2016px">Street Address :</div>
  <div class="abs field" style="left:336px;top:2010px;width:252px"></div>
  <div class="abs label" style="left:614px;top:2016px">City :</div>
  <div class="abs field" style="left:849px;top:2010px;width:250px"></div>

  <div class="abs label" style="left:101px;top:2077px">State :</div>
  <div class="abs field" style="left:336px;top:2071px;width:252px"></div>
  <div class="abs label" style="left:614px;top:2077px">ZIP Code :</div>
  <div class="abs field" style="left:849px;top:2071px;width:250px"></div>

  <div class="abs sub-head">Pick-Up Location if Other Than Residence</div>
  <div class="abs check" style="left:194px;top:2204px"><i class="on"></i>Airport</div>
  <div class="abs check" style="left:395px;top:2204px"><i></i>Seaport</div>
  <div class="abs check" style="left:595px;top:2204px"><i></i>Private Aviation</div>
  <div class="abs check" style="left:795px;top:2204px"><i></i>Hotel or Restaurant</div>

  <div class="abs note-label">Flight, Hotel, Cruise Information</div>
  <div class="abs field" style="left:103px;top:2304px;width:998px;height:82px"></div>

  <div class="abs btn-light">Submit</div>
  <div class="abs btn-ghost">Enter More Details</div>
</section>

<footer>
  <div class="abs footnav">Home<span>|</span>About Us<span>|</span>Available Services<span>|</span>Service Area<span>|</span>On-Line Reservations<span>|</span>Credit Card Form<span>|</span>Our Fleet<span>|</span>Contact Us</div>
  <div class="abs footrule"></div>
  <div class="abs copyright">Copyright © yourwebsite &nbsp;|&nbsp; Terms &amp; Conditions &nbsp;|&nbsp; Privacy Policy</div>
  <div class="abs social"><i></i><i></i><i></i><i></i></div>
</footer>

</body>
</html>
```